Business card design

I need my logo on this card, things I need the card to have on it
licensed and insured.
owner operators Milo & Trent Halvorsen
my phone number 5083716254
Disaster Recovery, Storm Damage Restoration, Proactive Disaster Plan Management, Roof Repair/Restoration Structural Repair and Reconstruction, Emergency Boarding and Tarping Service, Perimeter Fencing, Emergency Tree Removal,

```html
<!DOCTYPE html>
<html lang="en">
<head>
<meta charset="utf-8">
<title>Halvorsen's Construction — Business Card</title>
<link href="https://fonts.googleapis.com/css2?family=Montserrat:wght@300;400;500&display=swap" rel="stylesheet">
<style>
  :root {
    --stage: #050505;
    --card-blue: #1d5fe0;
    --band-teal: #2a8aa6;
    --band-teal-soft: #3f9fb3;
    --ink-white: #ffffff;
    --photo-sky: #ece4cc;
    --photo-warm: #cdb98f;
    --photo-deep: #55442f;
  }
  * { margin: 0; padding: 0; box-sizing: border-box; }
  html, body {
    width: 1200px;
    height: 675px;
    overflow: hidden;
    background: var(--stage);
    font-family: "Montserrat", sans-serif;
    color: var(--ink-white);
  }
  .canvas {
    width: 1200px;
    height: 675px;
    display: flex;
    align-items: center;
    justify-content: center;
    gap: 50px;
  }
  .card {
    position: relative;
    width: 520px;
    height: 297px;
    background: var(--card-blue);
    overflow: hidden;
  }

  /* Front */
  .card-front {
    display: flex;
    flex-direction: column;
    align-items: center;
    justify-content: center;
    text-align: center;
  }
  .brand {
    display: flex;
    align-items: center;
    gap: 10px;
  }
  .brand-mark {
    width: 14px;
    height: 14px;
    background: var(--ink-white);
    flex: none;
  }
  .brand-name {
    font-weight: 300;
    font-size: 34px;
    letter-spacing: 1px;
    line-height: 1;
  }
  .brand-sub {
    margin-top: 6px;
    font-weight: 300;
    font-size: 10px;
    letter-spacing: 6px;
    text-transform: uppercase;
  }
  .owners {
    margin-top: 16px;
    font-size: 15px;
    font-weight: 400;
  }
  .phone {
    margin-top: 4px;
    font-size: 15px;
    font-weight: 400;
  }

  /* Back */
  .card-back .side-band {
    position: absolute;
    top: 0; bottom: 0; left: 0;
    width: 16px;
    background: linear-gradient(180deg, var(--band-teal-soft), var(--band-teal));
  }
  .back-brand {
    position: absolute;
    top: 22px;
    left: 44px;
  }
  .back-brand .brand { gap: 6px; }
  .back-brand .brand-mark { width: 8px; height: 8px; }
  .back-brand .brand-name { font-size: 17px; }
  .back-brand .brand-sub {
    margin-top: 3px;
    font-size: 5.5px;
    letter-spacing: 3px;
  }
  .services {
    position: absolute;
    top: 74px;
    left: 44px;
    list-style: none;
    font-size: 11.5px;
    font-weight: 400;
    line-height: 1.6;
  }
  .crew-photo {
    position: absolute;
    top: 0;
    right: 0;
    bottom: 0;
    width: 160px;
    background: linear-gradient(160deg, var(--photo-sky) 0%, var(--photo-warm) 45%, var(--photo-deep) 100%);
  }
</style>
</head>
<body>
  <main class="canvas">
    <section class="card card-front" aria-label="Card front">
      <div class="brand">
        <span class="brand-mark"></span>
        <span class="brand-name">HALVORSEN'S</span>
      </div>
      <div class="brand-sub">Construction L.L.C</div>
      <p class="owners">Milo &amp; Trent Halvorsen</p>
      <p class="phone">P: 508-371-6254</p>
    </section>

    <section class="card card-back" aria-label="Card back">
      <div class="side-band"></div>
      <div class="back-brand">
        <div class="brand">
          <span class="brand-mark"></span>
          <span class="brand-name">HALVORSEN'S</span>
        </div>
        <div class="brand-sub">Construction L.L.C</div>
      </div>
      <ul class="services">
        <li>Disaster Recovery</li>
        <li>Perimeter Fencing</li>
        <li>Emergency Tree Removal</li>
        <li>Roof Repair/Restoration</li>
        <li>Storm Damage Restoration</li>
        <li>Proactive Disaster Plan Management</li>
        <li>Structural Repair and Reconstruction</li>
        <li>Emergency Boarding and Tarping Service</li>
      </ul>
      <div class="crew-photo" role="img" aria-label="Photo of construction workers in hard hats and safety vests on a sunlit job site"></div>
    </section>
  </main>
</body>
</html>
```